Sexy stockings - 1 creative web page design needed!

We need a design for the main home page of our company 'Calder Hosiery'. Out company sells stockings for women in Australia and this will be an online shopping site.

I have mocked up an example showing the type of layout and text that is required:
http://www.calderhosiery.example.com.au

The design should have the same menu and text as shown in the example. A slider will be positioned in the middle of the page promoting certain styles.

The page currently has a width of 800px.

What I am looking for is some genuine design flare. Good use of fonts, stylish menu and interesting background. Also please note, this is the will be the home page so please keep text to a minimum.

An example of stylish menus can be seen here: (See 22, 26, 41)
http://plumtrellis.example.com/design-showcase-inspiration/50-stylish-navigation-menus-for-design-inspiration/

An example of creative footers:
http://www.brankloft.example.com/2009/01/40-nice-and-creative-website-footer-designs/

(See 22, 26, 41)

Update: I would like a banner picture at the top with the logo and title overlaid. Also some areas where I could advertise specials and 1 day delivery in the Metro area.

Only one page is required to be designed. No coding of links, slider etc is needed.

The deliverable will be one photoshop project file.
Updates

So far the designs submitted have not been very creative. I am not interested in a plain design where you have just copy and pasted the pictures I  have supplied and changed the background colour - I could do this myself in Photoshop. What I am looking for is some genuine design flare. Good use of fonts, stylish menu and interesting background.

Also note - this is a home page, so there should be minimal text. 

Once a quality design has been submitted, I will guarantee this project.

Reason: I have extended the deadline in order for designers to submit their new designs for the following update to the brief: I have decided a banner picture at the top with the logo and title overlaid would look great. Also can I have some areas on the page where I could advertise specials and 1 day delivery in the Metro area.

Target Market(s)

We are marketing this product to the sophisticated professional woman.

Industry/Entity Type

Online Shopping

Requirements
Must have
• Must have the subtitle - "Signature Italian Stockings"

Logo picture incorporated somewhere on page. (Do not include "Sheer Silky Stockings" from packaging.)

The style of the webpage should be consistent with the packaging.

Please see the attached files.
Nice to have
• A creative background pattern - maybe incorporate the logo.
Should not have
• I am looking for a CREATIVE design, do not submit a design that has is just the supplied pictures copy and pasted in a different layout. (I could easily do that myself).

```html
<!DOCTYPE html>
<html lang="en">
<head>
<meta charset="utf-8">
<title>Calder Hosiery — Home</title>
<link rel="stylesheet" href="https://fonts.googleapis.com/css2?family=Rokkitt:wght@400;700&family=Arimo:wght@400;700&display=swap">
<style>
  :root {
    --charcoal: #47464c;
    --charcoal-dark: #3c3b41;
    --charcoal-light: #5f5e64;
    --blush: #c9a0a2;
    --blush-light: #f3cfd0;
    --blush-pale: #f9e3e3;
    --blush-text: #e8aeb0;
    --panel: #ffffff;
    --ink: #3a3a40;
    --white: #ffffff;
  }
  * { box-sizing: border-box; margin: 0; padding: 0; }
  html, body { width: 1200px; height: 828px; overflow: hidden; }
  body {
    position: relative;
    background: var(--charcoal);
    font-family: "Rokkitt", Georgia, serif;
  }
  .backdrop {
    position: absolute; inset: 0 0 93px 0;
    background: linear-gradient(180deg, #4d4c52 0%, #46454b 60%, #424147 100%);
  }

  /* Header */
  .brand { position: absolute; left: 160px; top: 16px; width: 180px; }
  .brand-mark {
    position: absolute; left: 52px; top: 6px;
    width: 80px; height: 80px; border-radius: 50%;
    background: var(--blush-light); opacity: .85;
  }
  .brand-name {
    position: absolute; left: 6px; top: 92px;
    font-size: 46px; line-height: 1; color: var(--white); font-weight: 400;
    letter-spacing: 1px;
  }

  .topbar {
    position: absolute; left: 357px; top: 46px; width: 723px; height: 24px;
    background: var(--blush);
  }
  .cart {
    position: absolute; right: 80px; top: 0; height: 24px;
    display: flex; align-items: center; gap: 8px;
    font-family: "Arimo", Arial, sans-serif; font-size: 12px; color: var(--ink);
  }
  .cart-button {
    position: absolute; right: 0; top: 0; width: 73px; height: 24px;
    background: var(--blush-light);
    font-family: "Arimo", Arial, sans-serif; font-size: 12px; font-weight: 700;
    color: var(--ink); display: flex; align-items: center; justify-content: center;
  }

  .main-nav { position: absolute; left: 370px; top: 46px; }
  .nav-tab {
    position: absolute; top: 0; width: 95px; height: 94px;
  }
  .nav-tab svg { position: absolute; inset: 0; }
  .nav-link {
    position: absolute; top: 38px;
    font-size: 14px; color: var(--white); text-transform: uppercase;
    letter-spacing: .3px; white-space: nowrap;
  }
  .nav-link.is-active {
    left: 0; width: 95px; text-align: center;
    font-size: 13px; letter-spacing: 0; color: var(--blush-text);
  }

  /* Content panel */
  .content {
    position: absolute; left: 120px; top: 168px; width: 960px; height: 567px;
    background: linear-gradient(180deg, #fbfbfb, #f1f1f1);
    border: 1px solid var(--blush);
  }
  .specials { position: absolute; left: 19px; top: 17px; width: 211px; height: 398px; }
  .specials svg { position: absolute; inset: 0; }
  .specials-title {
    position: absolute; top: 16px; width: 100%; text-align: center;
    font-size: 18px; font-weight: 400; color: var(--blush-text); letter-spacing: .5px;
  }
  .specials-list { position: absolute; top: 59px; width: 100%; list-style: none; }
  .specials-list li {
    text-align: center; color: var(--white); font-size: 15px; line-height: 17px;
    margin-bottom: 36px;
  }
  .specials-seal {
    position: absolute; left: 82px; top: 275px; width: 46px; height: 46px;
    border-radius: 50%; background: var(--blush-light);
  }

  .delivery {
    position: absolute; left: 27px; top: 442px; width: 196px; height: 93px;
    background: linear-gradient(135deg, #f6d4d4, #eebfc0);
    box-shadow: 0 2px 5px rgba(0,0,0,.25);
    padding: 5px;
  }
  .delivery-inner {
    width: 100%; height: 100%; border: 1px solid var(--blush);
    display: flex; align-items: center; justify-content: center; text-align: center;
    font-size: 16px; font-weight: 700; line-height: 20px; color: var(--ink);
  }

  .slider {
    position: absolute; left: 250px; top: 17px; width: 691px; height: 518px;
    border: 1px solid var(--blush); background: var(--white);
  }
  .slide-visual {
    position: absolute; left: 1px; top: 1px; right: 1px; bottom: 1px;
    background: radial-gradient(ellipse at 55% 48%, #6a686e 0%, #9a8f92 34%, #e8cfd0 52%, #ffffff 72%);
  }
  .slider-arrow {
    position: absolute; top: 235px; width: 36px; height: 36px;
    background: var(--white); border: 1px solid var(--blush-light);
  }
  .slider-arrow.prev { left: 0; }
  .slider-arrow.next { right: 0; }
  .slider-dots { position: absolute; left: 9px; bottom: 9px; display: flex; gap: 4px; }
  .slider-dots span { width: 9px; height: 9px; border: 1px solid var(--blush); background: var(--white); }
  .slider-dots span.is-current { background: var(--blush); }

  /* Footer */
  .site-footer {
    position: absolute; left: 0; top: 737px; width: 1200px; height: 91px;
    background: linear-gradient(90deg, #efc4c5 0%, #f7dcdc 50%, #f2cccd 100%);
    border-top: 2px solid #e6b6b7;
    font-family: "Arimo", Arial, sans-serif; color: var(--ink);
  }
  .footer-nav {
    position: absolute; left: 367px; top: 18px; height: 56px;
    border-left: 1px solid var(--charcoal); padding-left: 9px; list-style: none;
  }
  .footer-nav li { font-size: 12px; font-weight: 700; line-height: 19.5px; }
  .footer-info { position: absolute; right: 142px; top: 23px; text-align: right; }
  .footer-name { font-size: 11px; font-weight: 700; line-height: 12px; }
  .footer-tagline { font-size: 9.5px; font-weight: 700; line-height: 11px; }
  .footer-copy { font-size: 9.5px; font-weight: 700; margin-top: 14px; }
</style>
</head>
<body>
  <div class="backdrop" role="img" aria-label="Charcoal background with a faint repeating brand-name pattern"></div>

  <header class="site-header">
    <div class="brand">
      <span class="brand-mark" aria-hidden="true"></span>
      <span class="brand-name">calder</span>
    </div>

    <div class="topbar">
      <div class="cart">
        <svg width="18" height="14" viewBox="0 0 18 14" aria-hidden="true">
          <path d="M1 1h3l2.2 8h8.3l2-6H5" fill="none" stroke="#3a3a40" stroke-width="1.6"/>
          <circle cx="7.5" cy="12" r="1.4" fill="#3a3a40"/><circle cx="13.5" cy="12" r="1.4" fill="#3a3a40"/>
        </svg>
        <span>0 Items</span>
      </div>
      <a class="cart-button">View Cart</a>
    </div>

    <nav class="main-nav">
      <div class="nav-tab">
        <svg width="95" height="94" viewBox="0 0 95 94" aria-hidden="true">
          <defs>
            <linearGradient id="tabFill" x1="0" y1="0" x2="0" y2="1">
              <stop offset="0" stop-color="#5a595f"/><stop offset="1" stop-color="#3e3d43"/>
            </linearGradient>
          </defs>
          <path d="M0 0H95V92L47.5 74L0 92Z" fill="url(#tabFill)"/>
          <path d="M3 0V86M92 0V86" stroke="#c9a0a2" stroke-width="1"/>
        </svg>
        <a class="nav-link is-active">Collection</a>
      </div>
      <a class="nav-link" style="left:144px">News</a>
      <a class="nav-link" style="left:242px">About</a>
    </nav>
  </header>

  <main class="content">
    <aside class="specials">
      <svg width="211" height="398" viewBox="0 0 211 398" aria-hidden="true">
        <defs>
          <radialGradient id="ribbonFill" cx="0.5" cy="0.5" r="0.7">
            <stop offset="0" stop-color="#6b6a70"/><stop offset="1" stop-color="#404045"/>
          </radialGradient>
        </defs>
        <path d="M0 0H211V398L105.5 350L0 398Z" fill="url(#ribbonFill)"/>
        <path d="M4 0V390M207 0V390" stroke="#c9a0a2" stroke-width="1"/>
      </svg>
      <h2 class="specials-title">CALDER SPECIALS</h2>
      <ul class="specials-list">
        <li>Winter Collection<br>2011</li>
        <li>Spring Collection<br>2011</li>
        <li>Summer Collection<br>2012</li>
      </ul>
      <span class="specials-seal" role="img" aria-label="Small blush floral seal"></span>
    </aside>

    <div class="delivery">
      <p class="delivery-inner">One Day Delivery in<br>the Metro Area.</p>
    </div>

    <section class="slider">
      <div class="slide-visual" role="img" aria-label="Featured slide: charcoal gift box with blush drawer and branded tissue paper"></div>
      <a class="slider-arrow prev" aria-label="Previous slide">
        <svg width="34" height="34" viewBox="0 0 34 34"><path d="M21 7L11 17L21 27" fill="none" stroke="#e3a9ab" stroke-width="1.5"/></svg>
      </a>
      <a class="slider-arrow next" aria-label="Next slide">
        <svg width="34" height="34" viewBox="0 0 34 34"><path d="M13 7L23 17L13 27" fill="none" stroke="#e3a9ab" stroke-width="1.5"/></svg>
      </a>
      <div class="slider-dots"><span class="is-current"></span><span></span><span></span><span></span><span></span></div>
    </section>
  </main>

  <footer class="site-footer">
    <ul class="footer-nav">
      <li>Collection</li>
      <li>News</li>
      <li>About</li>
    </ul>
    <div class="footer-info">
      <p class="footer-name">Calder</p>
      <p class="footer-tagline">Signature Italian Stockings</p>
      <p class="footer-copy">© Copyright 2012 Calder Hosiery</p>
    </div>
  </footer>
</body>
</html>
```